BildeVOLD buisnesscard

Hey :) I need a modern buisnesscard for my company BildeVOLD
It most have:
Dagligleder og Fotograf: Henrik Audun Strandvik

Mob: +4791264085
Epost: post@bildevold.example
Adresse: Kvernbakken9, 6040 Fjordvik

Facbook and instagram logo with text BildeVOLD

BildeVOLD logo

It Company

```html
<!DOCTYPE html>
<html lang="no">
<head>
<meta charset="utf-8">
<title>BildeVOLD – business card</title>
<link rel="stylesheet" href="https://fonts.googleapis.com/css2?family=Montserrat:wght@400;500;600;700&display=swap">
<style>
  :root {
    --backdrop: #2b2b2b;
    --card-black: #050505;
    --card-white: #ffffff;
    --mark-grey: #a9a9a9;
    --text-light: #e6e6e6;
    --text-soft: #c9c9c9;
    --divider: #bdbdbd;
  }
  * { margin: 0; padding: 0; box-sizing: border-box; }
  html, body {
    width: 1200px;
    height: 900px;
    overflow: hidden;
    background: var(--backdrop);
    font-family: "Montserrat", sans-serif;
  }
  .stage {
    position: relative;
    width: 1200px;
    height: 900px;
  }
  .card {
    position: absolute;
    left: 330px;
    width: 540px;
    height: 310px;
    border-radius: 24px;
    overflow: hidden;
  }
  .card--front {
    top: 110px;
    background: var(--card-black);
    display: flex;
    flex-direction: column;
    align-items: center;
    justify-content: center;
  }
  .front-name {
    color: var(--mark-grey);
    font-weight: 700;
    font-size: 54px;
    letter-spacing: 1px;
    margin-top: 20px;
  }
  .front-social {
    margin-top: 56px;
    display: flex;
    flex-direction: column;
    align-items: center;
    gap: 6px;
    color: var(--text-soft);
    font-size: 13px;
    font-weight: 500;
  }
  .front-social__dot {
    width: 9px;
    height: 9px;
    border: 1.5px solid var(--text-soft);
    border-radius: 2px;
  }
  .card--back {
    top: 480px;
    display: flex;
    background: var(--card-black);
  }
  .back-brand {
    width: 235px;
    background: var(--card-white);
    border-right: 3px solid var(--divider);
    display: flex;
    align-items: center;
    justify-content: center;
  }
  .back-brand__name {
    color: var(--mark-grey);
    font-weight: 700;
    font-size: 34px;
  }
  .back-contact {
    flex: 1;
    display: flex;
    flex-direction: column;
    align-items: center;
    justify-content: center;
    text-align: center;
    color: var(--text-light);
  }
  .contact-name {
    font-size: 18px;
    font-weight: 600;
  }
  .contact-role {
    font-size: 13px;
    color: var(--text-soft);
    margin-top: 2px;
  }
  .contact-icons {
    display: flex;
    gap: 6px;
    margin: 8px 0 6px;
  }
  .contact-icons svg { width: 10px; height: 10px; fill: var(--text-soft); }
  .contact-line {
    font-size: 13px;
    line-height: 1.45;
    color: var(--text-light);
  }
</style>
</head>
<body>
<main class="stage">
  <section class="card card--front">
    <div class="front-name">BildeVOLD</div>
    <div class="front-social">
      <span class="front-social__dot"></span>
      <span>BildeVOLD</span>
    </div>
  </section>

  <section class="card card--back">
    <div class="back-brand">
      <span class="back-brand__name">BildeVOLD</span>
    </div>
    <div class="back-contact">
      <div class="contact-name">Henrik Audun Strandvik</div>
      <div class="contact-role">Dagligleder og Fotograf</div>
      <div class="contact-icons">
        <svg viewBox="0 0 24 24" aria-label="phone"><path d="M6.6 10.8a15 15 0 0 0 6.6 6.6l2.2-2.2a1 1 0 0 1 1-.25 11.4 11.4 0 0 0 3.6.57 1 1 0 0 1 1 1V20a1 1 0 0 1-1 1A17 17 0 0 1 3 4a1 1 0 0 1 1-1h3.5a1 1 0 0 1 1 1c0 1.25.2 2.450.57 3.6a1 1 0 0 1-.25 1z"/></svg>
        <svg viewBox="0 0 24 24" aria-label="email"><path d="M2 5h20v14H2z M4 7v.5l8 5 8-5V7l-8 5z" fill-rule="evenodd"/></svg>
        <svg viewBox="0 0 24 24" aria-label="location"><path d="M12 2a7 7 0 0 0-7 7c0 5.2 7 13 7 13s7-7.8 7-13a7 7 0 0 0-7-7zm0 9.5A2.5 2.5 0 1 1 12 6.5a2.5 2.5 0 0 1 0 5z"/></svg>
      </div>
      <div class="contact-line">+4791264085</div>
      <div class="contact-line">post@bildevold.example</div>
      <div class="contact-line">Kvernbakken9, 6040 Fjordvik</div>
    </div>
  </section>
</main>
</body>
</html>
```